QVR business card

Need a business card for a company that provides instructional design and elearning development services. The website is here: http://quorvane.studio/

I'm attaching a current logo, as well as the old business card design. While I like to keep it clean, the old design is too simplistic for my liking. The only idea I want to reuse from the old design is placing industry jargon on the back of the card, just need a better way to present it. But if you have other ideas for the back--feel free to experiment.

Please use the colors complementary to the color we have on the website. Thank you!

```html
<!DOCTYPE html>
<html lang="en">
<head>
<meta charset="utf-8">
<title>QVR business card</title>
<link rel="stylesheet" href="https://fonts.googleapis.com/css2?family=Montserrat:wght@600;700;800&family=Lato:wght@400;700&display=swap">
<style>
  :root {
    --canvas: #ece9e2;
    --paper: #ffffff;
    --sand: #dccb8c;
    --ink: #1f1f1f;
    --ink-soft: #2a2a2a;
    --teal: #1fb3a3;
    --gold: #e3d193;
  }
  * { box-sizing: border-box; margin: 0; padding: 0; }
  html, body { width: 1200px; height: 891px; overflow: hidden; }
  body {
    background: var(--canvas);
    font-family: "Lato", sans-serif;
    position: relative;
  }
  .card {
    position: absolute;
    top: 296px;
    width: 520px;
    height: 298px;
    border-radius: 6px;
    overflow: hidden;
    box-shadow: 0 10px 28px rgba(0,0,0,.18);
  }
  /* Front */
  .card-front { left: 50px; background: var(--sand); }
  .front-top {
    position: absolute; left: 0; top: 0; right: 0; height: 132px;
    background: var(--paper);
    border-bottom: 6px solid var(--paper);
    box-shadow: 0 4px 0 var(--sand), 0 8px 0 var(--paper);
  }
  .brand {
    position: absolute; left: 188px; top: 40px;
    display: flex; align-items: center; gap: 14px;
  }
  .brand-mark { width: 34px; height: 34px; background: var(--teal); }
  .brand-name {
    font-family: "Montserrat", sans-serif;
    font-weight: 800; font-size: 46px; letter-spacing: 4px;
    color: var(--teal);
  }
  .holder-name {
    position: absolute; left: 30px; top: 168px;
    font-family: "Montserrat", sans-serif;
    font-weight: 700; font-size: 22px; color: var(--ink);
  }
  .contacts {
    position: absolute; right: 0; top: 160px; width: 300px;
    display: flex; flex-direction: column; gap: 9px;
    list-style: none;
  }
  .contact {
    display: flex; align-items: center; height: 32px;
    background: var(--ink);
  }
  .contact-icon {
    width: 32px; height: 32px; display: flex; align-items: center; justify-content: center;
    border-right: 3px solid var(--sand);
  }
  .contact-icon svg { width: 18px; height: 18px; }
  .contact-text {
    padding-left: 12px; color: var(--gold);
    font-size: 15px; letter-spacing: .2px;
  }
  /* Back */
  .card-back {
    left: 630px; background: var(--ink-soft);
    display: flex; flex-direction: column; justify-content: center; align-items: center;
    text-align: center; padding: 0 28px;
    font-family: "Montserrat", sans-serif;
  }
  .jargon {
    color: var(--teal); font-weight: 700; font-size: 15.5px;
    letter-spacing: 1px; line-height: 1.2; text-transform: uppercase;
  }
  .headline {
    color: var(--gold); font-weight: 800; font-size: 36px;
    letter-spacing: 2px; margin: 16px 0; text-transform: uppercase;
  }
</style>
</head>
<body>
  <section class="card card-front" aria-label="Card front">
    <div class="front-top">
      <div class="brand">
        <span class="brand-mark"></span>
        <span class="brand-name">QVR</span>
      </div>
    </div>
    <p class="holder-name">Marcus Delvane</p>
    <ul class="contacts">
      <li class="contact">
        <span class="contact-icon">
          <svg viewBox="0 0 24 24" fill="var(--gold)"><path d="M6.6 10.8a15.1 15.1 0 0 0 6.6 6.6l2.2-2.2a1 1 0 0 1 1-.25 11.4 11.4 0 0 0 3.6.6 1 1 0 0 1 1 1V20a1 1 0 0 1-1 1A17 17 0 0 1 3 4a1 1 0 0 1 1-1h3.5a1 1 0 0 1 1 1c0 1.25.2 2.45.6 3.6a1 1 0 0 1-.25 1z"/></svg>
        </span>
        <span class="contact-text">555-014-2290</span>
      </li>
      <li class="contact">
        <span class="contact-icon">
          <svg viewBox="0 0 24 24" fill="none" stroke="var(--gold)" stroke-width="2"><rect x="3" y="5" width="18" height="14"/><path d="M3 5l9 8 9-8"/></svg>
        </span>
        <span class="contact-text">mdelvane@quorvane.studio</span>
      </li>
      <li class="contact">
        <span class="contact-icon">
          <svg viewBox="0 0 24 24" fill="none" stroke="var(--gold)" stroke-width="2"><circle cx="12" cy="12" r="9"/><path d="M3 12h18M12 3c3 3 3 15 0 18M12 3c-3 3-3 15 0 18"/></svg>
        </span>
        <span class="contact-text">www.quorvane.studio</span>
      </li>
    </ul>
  </section>

  <section class="card card-back" aria-label="Card back">
    <p class="jargon">Mobile learning SCORM instructional<br>design LMS MOOCs eLearning HTML5</p>
    <h1 class="headline">How can we help?</h1>
    <p class="jargon">Adult learning theory gamification<br>classroom xAPI blended learning</p>
  </section>
</body>
</html>
```